Copperleaf Balustrade Website Redesign

I want a fresh new design for my website. Original website
www.copperleafbalustrade-example.com. Will need to add additional photos for winning designer. Please use the basic layout for new design. Looking to get a more modern, functional site to attract new customer and ne bale to highlight past projects. Need it to be easy to navigate and get in touch with me for inquiries.

Target Market(s)

Builders and home owners in WA state

Industry/Entity Type

Building, Construction, Deck building

Coding

Coded - Design and coding required

Number of Pages Required

5+ page

Font styles to use
Sans Serif

Colors
0054AA
0677BA
7BADD7
CADEEF
E8F1F8
0094D4
00A9DD
6FCCEA
C7EBF8
E9F6FB
00AB8E
00BBA5
67D7C9
C6EFE9
E9F9F6
59FF00
82FF00
B8FF75
E3FFCB
F4FFEA

Requirements
Must have
• Will need to add more photos of completed projects
Nice to have
• Fresh take on old website, something modern
Should not have
• Nothing comes to mind

```html
<!DOCTYPE html>
<html lang="en">
<head>
<meta charset="utf-8">
<title>Copperleaf Balustrade</title>
<link rel="stylesheet" href="https://fonts.googleapis.com/css2?family=Jost:wght@300;400;500&family=Lato:wght@400;700;900&display=swap">
<style>
:root{
  --green:#175a30;
  --green-dark:#0f4322;
  --teal:#00AB8E;
  --teal-soft:#00BBA5;
  --mint:#E9F9F6;
  --mint-mid:#C6EFE9;
  --sky:#E9F6FB;
  --blue:#0054AA;
  --ink:#1e1e1e;
  --text:#333;
  --muted:#555;
  --bar:#1c1c1c;
  --white:#fff;
}
*{box-sizing:border-box;margin:0;padding:0}
html,body{width:1200px;height:5068px;overflow:hidden}
body{font-family:"Lato",sans-serif;color:var(--text);background:var(--white);position:relative}
.abs{position:absolute}
.heading{font-family:"Jost",sans-serif;font-weight:300;color:var(--ink);text-transform:uppercase;letter-spacing:.5px}
.underline{display:inline-block;border-bottom:2px solid var(--teal);line-height:1}
.btn{display:inline-block;background:var(--green);color:#fff;font-weight:700;font-size:14px;text-transform:uppercase;padding:14px 24px;border-radius:3px;letter-spacing:.2px}
/* top bar */
.topbar{left:0;top:0;width:1200px;height:46px;background:var(--bar);color:#ddd;font-size:13px}
.topbar .contact-item{top:15px;display:flex;align-items:center;gap:8px}
.social{display:flex;gap:6px}
.social span{width:34px;height:34px;border-radius:50%;border:2px solid #fff;background:#2a2a2a;display:block}
/* nav */
.nav{left:0;top:46px;width:1200px;height:78px;background:#fff}
.nav a{position:absolute;top:30px;font-size:14px;font-weight:700;color:var(--ink);text-decoration:none;text-transform:uppercase}
.nav .active{color:var(--green);border-bottom:2px solid var(--teal);padding-bottom:2px}
.nav .sep{position:absolute;top:0;width:1px;height:78px;background:#e6e6e6}
.quote{left:917px;top:0;width:171px;height:78px;background:var(--green);color:#fff;font-weight:700;font-size:14px;display:flex;align-items:center;justify-content:center;text-transform:uppercase}
.brand{left:507px;top:0;width:186px;height:200px;z-index:3}
.brand-name{position:absolute;left:0;top:40px;width:186px;text-align:center;font-weight:700;color:var(--green);font-size:19px;line-height:1.3;text-transform:uppercase}
/* hero */
.hero{left:0;top:124px;width:1200px;height:536px;background:linear-gradient(180deg,#3d4a3f 0%,#5b5a52 35%,#6a4f3d 65%,#3e4b35 100%)}
.hero-copy{left:0;top:294px;width:1200px;text-align:center;color:#fff}
.hero-copy .kicker{font-size:19px;font-weight:700;text-transform:uppercase;line-height:1}
.hero-copy h1{font-family:"Jost",sans-serif;font-weight:500;font-size:60px;line-height:1;margin-top:18px;letter-spacing:1px}
.hero-copy .sub{font-family:"Jost",sans-serif;font-weight:300;font-size:31px;line-height:1;margin-top:16px}
.hero-copy .btn{margin-top:28px;padding:12px 24px}
.tab{background:#6d6d6d;color:#fff;font-weight:700;font-size:16px;display:flex;align-items:center;justify-content:center;text-transform:uppercase}
.tab span{writing-mode:vertical-rl;transform:rotate(180deg);letter-spacing:.5px}
.tab.right span{transform:none}
.photo{display:block}
.feature{left:600px;top:610px;width:270px;height:312px;background:var(--green);color:#fff;padding:26px 24px}
.feature h3{font-family:"Jost",sans-serif;font-weight:400;font-size:24px;line-height:1.3;text-transform:uppercase}
.feature p{font-size:13px;line-height:1.65;margin-top:14px}
.feature .light-btn{display:inline-block;margin-top:14px;background:#fff;color:var(--ink);font-size:13px;font-weight:700;padding:14px 20px;border-radius:3px;text-transform:uppercase}
/* about */
.about{left:110px;top:1010px;width:980px;text-align:center}
.about h2{font-size:38px}
.about .sub{color:var(--green);font-size:22px;font-weight:700;margin-top:22px}
.about p{font-size:16.5px;line-height:1.75;margin-top:18px;color:var(--text)}
.about .btn{margin-top:30px}
/* why */
.why{left:0;top:1556px;width:1200px;height:618px;background:linear-gradient(180deg,#6b7077 0%,#55595f 100%)}
.why h2{position:absolute;left:0;top:74px;width:1200px;text-align:center;color:#fff;font-size:38px}
.why h2 .underline{border-color:#fff}
.card{position:absolute;width:427px;height:179px;background:#fff;border-radius:8px}
.card.left{text-align:right;padding:26px 70px 0 40px}
.card.right{text-align:left;padding:26px 34px 0 70px}
.card h4{font-size:14.5px;font-weight:700;color:var(--ink);text-transform:uppercase}
.card.left h4{text-align:left;padding-left:4px}
.card p{font-size:12.5px;line-height:1.6;color:var(--muted);margin-top:14px}
.badge{position:absolute;width:92px;height:92px;border-radius:50%;background:#fff;display:flex;align-items:center;justify-content:center}
.badge .inner{width:76px;height:76px;border-radius:50%;background:var(--mint);display:flex;align-items:center;justify-content:center}
.badge .inner.solid{background:var(--green)}
/* process */
.process{left:0;top:2174px;width:1200px;height:472px;background:var(--sky)}
.process h2{position:absolute;left:0;top:72px;width:1200px;text-align:center;font-size:38px}
.step{position:absolute;top:152px;width:300px;text-align:center}
.step .ring{width:116px;height:116px;border-radius:50%;margin:0 auto;display:flex;align-items:center;justify-content:center;background:#6d6d6d}
.step .ring.on{background:var(--green)}
.step .ring .dash{width:104px;height:104px;border-radius:50%;border:2px dashed #fff;display:flex;align-items:center;justify-content:center}
.step h4{font-size:16px;font-weight:700;color:var(--ink);margin-top:36px;text-transform:uppercase}
.step p{font-size:13px;line-height:1.65;color:var(--muted);margin-top:16px}
/* serving */
.serving-frame{left:110px;top:2764px;width:457px;height:383px;background:#dedede}
.serving-photo{left:146px;top:2797px;width:454px;height:386px;background:linear-gradient(180deg,#8fb1cf 0%,#c7b8a8 45%,#6b6157 75%,#3d3a3a 100%)}
.serving-copy{left:667px;top:2790px;width:421px}
.serving-copy h2{font-size:38px;line-height:1.25}
.serving-copy .rule{width:82px;height:2px;background:var(--teal);margin-top:8px}
.serving-copy p{font-size:15px;line-height:1.7;text-align:justify;margin-top:30px;color:var(--text)}
.serving-copy .btn{margin-top:34px}
/* contact */
.contact{left:0;top:3305px;width:1200px;height:565px;background:linear-gradient(135deg,#145f31 0%,#1a6b3a 50%,#155a2f 100%);color:#fff;text-align:center}
.contact h2{position:absolute;left:0;top:54px;width:1200px;color:#fff;font-size:38px}
.contact h2 .underline{border-color:#fff}
.contact .sub{position:absolute;left:0;top:128px;width:1200px;font-size:22px;font-weight:700}
.contact .lead{position:absolute;left:210px;top:172px;width:780px;font-size:17px;line-height:1.7}
.field{position:absolute;background:#fff;border-radius:4px;color:#555;font-size:13px;text-align:left;padding:16px 18px}
.send{position:absolute;left:510px;top:3759px;width:178px;height:47px;background:var(--bar);color:#fff;font-size:14px;font-weight:700;border-radius:3px;display:flex;align-items:center;justify-content:center;text-transform:uppercase}
/* projects */
.projects h2{position:absolute;left:0;top:3952px;width:1200px;text-align:center;font-size:38px}
.proj{position:absolute}
/* footer */
.footer{left:0;top:4678px;width:1200px;height:390px;background:var(--bar);color:#ddd}
.footer h5{position:absolute;top:70px;color:#fff;font-size:15px;font-weight:700;text-transform:uppercase}
.footer h5::after{content:"";display:block;width:50px;height:2px;background:var(--teal);margin-top:10px}
.foot-brand{position:absolute;left:110px;top:118px;width:150px;text-align:center;color:#fff;font-size:25px;font-weight:400;line-height:1.35;text-transform:uppercase}
.foot-row{position:absolute;left:323px;display:flex;align-items:flex-start;gap:20px;font-size:13.5px;line-height:1.6;color:#eee}
.foot-row .dot{width:36px;height:36px;border-radius:50%;background:#fff;flex:none;display:flex;align-items:center;justify-content:center}
.links{position:absolute;left:638px;top:130px;font-size:14px;line-height:35px;color:#eee}
.newsletter{position:absolute;left:828px;top:128px;width:260px;height:45px;background:#fff;border-radius:3px;color:#555;font-size:13px;padding:14px 18px}
.foot-social{position:absolute;left:828px;top:212px;display:flex;gap:8px}
.foot-social span{width:34px;height:34px;border-radius:50%;border:2px solid #fff;display:block;background:#333}
.foot-social span.first{background:var(--green)}
.foot-line{position:absolute;left:110px;top:328px;width:1090px;height:1px;background:#3a3a3a}
.foot-bottom{position:absolute;top:348px;font-size:12px;color:#ddd}
</style>
</head>
<body>

<div class="abs topbar">
  <div class="abs contact-item" style="left:110px">
    <svg width="12" height="12" viewBox="0 0 24 24"><path fill="#00BBA5" d="M6.6 10.8c1.4 2.8 3.8 5.1 6.6 6.6l2.2-2.2c.3-.3.7-.4 1-.2 1.1.4 2.3.6 3.6.6.6 0 1 .4 1 1V20c0 .6-.4 1-1 1C10.6 21 3 13.4 3 4c0-.6.4-1 1-1h3.5c.6 0 1 .4 1 1 0 1.3.2 2.5.6 3.6.1.3 0 .7-.2 1z"/></svg>
    (509) 555-0148
  </div>
  <div class="abs contact-item" style="left:244px">
    <svg width="14" height="11" viewBox="0 0 24 18"><rect width="24" height="18" rx="2" fill="#00BBA5"/><path d="M2 2l10 8 10-8" stroke="#1c1c1c" stroke-width="2" fill="none"/></svg>
    hello@copperleafbalustrade-example.com
  </div>
  <div class="abs social" style="left:976px;top:6px"><span></span><span></span><span></span></div>
</div>

<nav class="abs nav">
  <a class="active" style="left:110px">Home</a>
  <span class="sep" style="left:174px"></span>
  <a style="left:187px">About Us</a>
  <span class="sep" style="left:283px"></span>
  <a style="left:293px">Products</a>
  <a style="left:804px">Contact</a>
  <div class="abs quote">Request a Quote</div>
</nav>
<div class="abs brand">
  <svg width="186" height="200" viewBox="0 0 186 200" style="position:absolute;left:0;top:0"><path d="M0 0H186V150L93 200L0 150Z" fill="#fff"/></svg>
  <div class="brand-name">Copperleaf<br>Balustrade</div>
</div>

<section class="abs hero" role="img" aria-label="Modern deck with cable railings and stairs overlooking a wooded garden"></section>
<div class="abs hero-copy">
  <div class="kicker">Licensed, Insured, &amp; Bonded</div>
  <h1>COPPERLEAF BALUSTRADE</h1>
  <div class="sub">Durable, stylish, and built for the Pacific Northwest.</div>
  <span class="btn">Get Started</span>
</div>
<div class="abs tab" style="left:110px;top:661px;width:77px;height:212px"><span>Glass Railings</span></div>
<div class="abs photo" style="left:187px;top:661px;width:143px;height:212px;background:linear-gradient(180deg,#9fbcd6 0%,#7f9a76 55%,#a26d45 100%)" role="img" aria-label="Deck with glass railing panels and a view"></div>
<div class="abs photo" style="left:330px;top:610px;width:270px;height:312px;background:linear-gradient(180deg,#e9e6e1 0%,#cfc8bd 50%,#7a6a58 100%)" role="img" aria-label="Indoor staircase with black aluminum railing"></div>
<div class="abs feature">
  <h3>Aluminum<br>Railings</h3>
  <p>For a sleek, low-maintenance option, our powder-coated aluminum railings provide strength, corrosion resistance, and a modern aesthetic.</p>
  <span class="light-btn">Learn More</span>
</div>
<div class="abs photo" style="left:870px;top:661px;width:140px;height:212px;background:linear-gradient(180deg,#b8c9d8 0%,#8c8f8a 50%,#5c6166 100%)" role="img" aria-label="Deck with cable railing and outdoor seating"></div>
<div class="abs tab right" style="left:1010px;top:661px;width:78px;height:212px"><span>Cable Railings</span></div>

<section class="abs about">
  <h2 class="heading">About Copperleaf Balustrade</h2>
  <div class="sub">Formed in 2020</div>
  <p>At Copperleaf Balustrade, we believe that every outdoor space deserves the perfect blend of style, safety, and durability. Serving homeowners, builders, and commercial developers across the Washington State, we specialize in crafting custom railing systems designed to withstand the region's unique climate while enhancing the beauty of your outdoor living spaces.</p>
  <p>With a focus on premium materials, expert craftsmanship, and exceptional customer service, Copperleaf Balustrade is proud to be the trusted partner for both residential and commercial railing projects. Whether you're looking to complement a new deck, add a modern touch to your balcony, or create a secure and stunning barrier for a commercial space, we've got the perfect solution for you.</p>
  <span class="btn">Learn More</span>
</section>

<section class="abs why" role="img" aria-label="Dim background of outdoor stairs with railings">
  <h2 class="heading">Why Choose <span class="underline">Copperleaf</span> Balustrade ?</h2>
  <div class="card left" style="left:116px;top:163px">
    <h4>Locally Crafted, Regionally Resilient</h4>
    <p>Our railings are designed with the Pacific Northwest's weather in mind—rain, snow, and everything in between. We use durable materials that are resistant to corrosion, moisture, and the elements, ensuring your railings stand the test of time.</p>
  </div>
  <div class="card right" style="left:655px;top:163px">
    <h4>Custom Solutions for Every Need</h4>
    <p>We work closely with you to design and fabricate custom railing systems that perfectly suit your space, style, and functional requirements. From intricate designs to minimalistic finishes, we tailor every project to your vision.</p>
  </div>
  <div class="card left" style="left:116px;top:362px">
    <h4 style="text-align:right">Expert Installation &amp; Craftsmanship</h4>
    <p>Our skilled craftsmen take pride in delivering exceptional workmanship, while our professional installers ensure every railing is securely mounted and aligned to meet local safety codes.</p>
  </div>
  <div class="card right" style="left:655px;top:362px">
    <h4>Full-Service Partner</h4>
    <p>From the initial consultation and design process to installation and ongoing maintenance, we are with you every step of the way to ensure your project exceeds expectations.</p>
  </div>
  <div class="badge" style="left:497px;top:207px"><div class="inner">
    <svg width="40" height="40" viewBox="0 0 40 40"><rect x="6" y="24" width="5" height="12" fill="#175a30"/><rect x="15" y="18" width="5" height="18" fill="#175a30"/><rect x="24" y="12" width="5" height="24" fill="#175a30"/><circle cx="32" cy="8" r="5" fill="none" stroke="#175a30" stroke-width="2.5"/></svg>
  </div></div>
  <div class="badge" style="left:609px;top:207px"><div class="inner">
    <svg width="40" height="40" viewBox="0 0 40 40"><circle cx="20" cy="15" r="9" fill="none" stroke="#175a30" stroke-width="3"/><rect x="15" y="25" width="10" height="8" rx="2" fill="#175a30"/></svg>
  </div></div>
  <div class="badge" style="left:497px;top:406px"><div class="inner">
    <svg width="40" height="40" viewBox="0 0 40 40"><path d="M8 18a12 12 0 0 1 24 0z" fill="#175a30"/><rect x="6" y="18" width="28" height="3" fill="#175a30"/><path d="M10 36c0-7 4-10 10-10s10 3 10 10z" fill="#175a30"/></svg>
  </div></div>
  <div class="badge" style="left:609px;top:406px"><div class="inner solid">
    <svg width="42" height="42" viewBox="0 0 42 42"><path d="M4 22l8-8 9 5 9-5 8 8-12 10z" fill="none" stroke="#fff" stroke-width="3" stroke-linejoin="round"/></svg>
  </div></div>
</section>

<section class="abs process">
  <h2 class="heading">Our <span class="underline">Process</span></h2>
  <div class="step" style="left:106px">
    <div class="ring"><div class="dash"><svg width="46" height="46" viewBox="0 0 46 46"><circle cx="23" cy="23" r="12" fill="none" stroke="#fff" stroke-width="5" stroke-dasharray="5 4"/><circle cx="23" cy="23" r="5" fill="#fff"/></svg></div></div>
    <h4>Consultation &amp; Design</h4>
    <p>We start by listening to your vision and understanding your specific needs. Our team will offer expert advice and design ideas to help you choose the best materials and styles.</p>
  </div>
  <div class="step" style="left:450px">
    <div class="ring on"><div class="dash"><svg width="46" height="46" viewBox="0 0 46 46"><path d="M10 10l26 26M36 10L10 36" stroke="#fff" stroke-width="5" stroke-linecap="round"/></svg></div></div>
    <h4>Professional Installation</h4>
    <p>Our experienced team handles all aspects of installation, from measuring to securing, ensuring your railing is safe, secure, and perfectly aligned.</p>
  </div>
  <div class="step" style="left:794px">
    <div class="ring"><div class="dash"><svg width="46" height="46" viewBox="0 0 46 46"><circle cx="23" cy="12" r="6" fill="#fff"/><path d="M8 32c6-6 10-6 15-4s9 2 15-2v6c-6 4-11 4-15 2s-9-2-15 2z" fill="#fff"/></svg></div></div>
    <h4>Ongoing Support</h4>
    <p>We offer warranties on all of our products and services, and we are always available to help with maintenance or modifications down the road.</p>
  </div>
</section>

<div class="abs serving-frame"></div>
<div class="abs serving-photo" role="img" aria-label="City skyline with an observation tower at sunset"></div>
<section class="abs serving-copy">
  <h2 class="heading">Serving<br>Washington State</h2>
  <div class="rule"></div>
  <p>Copperleaf Balustrade is proud to serve the entire state of Washington. Whether you're upgrading your home's deck or outfitting a commercial space, we understand the importance of creating beautiful, durable railings that stand up to the region's diverse and often challenging weather conditions.</p>
  <span class="btn">Contact Us</span>
</section>

<section class="abs contact">
  <h2 class="heading">Get in Touch <span class="underline">With Me</span> for Inquiries</h2>
  <div class="sub">Contact Us Today</div>
  <p class="lead">Ready to elevate your space with a custom railing solution that's built to last? Reach out to the Copperleaf Balustrade team for a free consultation. Let us bring your vision to life with craftsmanship, care, and precision.</p>
</section>
<div class="field" style="left:165px;top:3586px;width:283px;height:50px">Full Name</div>
<div class="field" style="left:458px;top:3586px;width:284px;height:50px">Phone</div>
<div class="field" style="left:751px;top:3586px;width:284px;height:50px">Email Address</div>
<div class="field" style="left:165px;top:3649px;width:870px;height:92px">Message</div>
<div class="send">Send Message</div>

<section class="projects">
  <h2 class="heading">Past <span class="underline">Projects</span></h2>
  <div class="proj" style="left:110px;top:4044px;width:480px;height:282px;background:linear-gradient(180deg,#8a8f86 0%,#b7ad8f 45%,#6f8f4f 100%)" role="img" aria-label="Backyard deck with black metal railing and a tree"></div>
  <div class="proj" style="left:608px;top:4044px;width:480px;height:282px;background:linear-gradient(180deg,#a9bfd3 0%,#7c8a6c 45%,#565a5e 100%)" role="img" aria-label="Hilltop deck with black aluminum railing"></div>
  <div class="proj" style="left:110px;top:4343px;width:315px;height:231px;background:linear-gradient(180deg,#c9ccd0 0%,#6f6c68 60%,#4d4a47 100%)" role="img" aria-label="Exterior stairs with black railing beside stone wall"></div>
  <div class="proj" style="left:443px;top:4343px;width:314px;height:231px;background:linear-gradient(180deg,#8f7f6c 0%,#b8bcbd 50%,#6d6459 100%)" role="img" aria-label="Glass panel railing on a new deck"></div>
  <div class="proj" style="left:773px;top:4343px;width:315px;height:231px;background:linear-gradient(180deg,#d0d6dc 0%,#8a8580 55%,#4b4845 100%)" role="img" aria-label="Balcony with horizontal black railing"></div>
</section>

<footer class="abs footer">
  <div class="foot-brand">Copperleaf<br>Balustrade</div>
  <h5 style="left:323px">Contact Us</h5>
  <h5 style="left:638px">Quick Links</h5>
  <h5 style="left:828px">Newsletter</h5>
  <div class="foot-row" style="top:130px">
    <span class="dot"><svg width="14" height="18" viewBox="0 0 14 18"><path d="M7 0a7 7 0 0 0-7 7c0 5 7 11 7 11s7-6 7-11a7 7 0 0 0-7-7z" fill="#175a30"/><circle cx="7" cy="7" r="2.5" fill="#fff"/></svg></span>
    <div>1420 Cedarline Rd, Yakima,<br>WA 98901</div>
  </div>
  <div class="foot-row" style="top:192px">
    <span class="dot"><svg width="16" height="16" viewBox="0 0 24 24"><path fill="#175a30" d="M6.6 10.8c1.4 2.8 3.8 5.1 6.6 6.6l2.2-2.2c.3-.3.7-.4 1-.2 1.1.4 2.3.6 3.6.6.6 0 1 .4 1 1V20c0 .6-.4 1-1 1C10.6 21 3 13.4 3 4c0-.6.4-1 1-1h3.5c.6 0 1 .4 1 1 0 1.3.2 2.5.6 3.6.1.3 0 .7-.2 1z"/></svg></span>
    <div>Call Us:<br>(509) 555-0148</div>
  </div>
  <div class="foot-row" style="top:254px">
    <span class="dot"><svg width="16" height="12" viewBox="0 0 24 18"><rect width="24" height="18" rx="2" fill="#175a30"/><path d="M2 2l10 8 10-8" stroke="#fff" stroke-width="2" fill="none"/></svg></span>
    <div>Email Us:<br>hello@copperleafbalustrade-example.com</div>
  </div>
  <div class="links">Home<br>About Us<br>Products<br>Contact us<br>Privacy Policy</div>
  <div class="newsletter">Email Address
    <svg width="16" height="16" viewBox="0 0 24 24" style="position:absolute;right:18px;top:14px"><path d="M2 12L22 3l-7 19-3-8z" fill="#175a30"/></svg>
  </div>
  <div class="foot-social"><span class="first"></span><span></span><span></span></div>
  <div class="foot-line"></div>
  <div class="foot-bottom" style="left:110px">WA GC LICENSE # COPPEBL914QX</div>
  <div class="foot-bottom" style="left:698px">Copyright © 2024 <b style="color:#fff">COPPERLEAF BALUSTRADE</b> / All Rights Reserved</div>
</footer>

</body>
</html>
```